Telecommunications/Power civil contractor needs business card design

Were a new telecommunications/power underground civil contractor that is looking for a new business card design. Our company colours are silver or grey and orange. Feel free to use the white background logo or the black background logo.

Target Market(s)

Local contractors, utility companies, private sector mining/energy companies, developers.

Industry/Entity Type

Telecommunications

Contact Information for Business Card

Each card will need the following info:
Persons name:
Title:
E-mail:
Phone number:
Shop Address:
Mailing Address:

Requirements
Must have
• Each card will need the following info:
• Persons name:
• Title:
• E-mail:
• Phone number:
• Shop Address:
• Mailing Address:

```html
<!DOCTYPE html>
<html lang="en">
<head>
<meta charset="utf-8">
<title>Tandem Line Contracting Inc — Business Card</title>
<link rel="stylesheet" href="https://fonts.googleapis.com/css2?family=Source+Sans+3:wght@400;600;700&display=swap">
<style>
  :root {
    --orange: #f15a24;
    --grey: #666666;
    --grey-dark: #5a5a5a;
    --white: #ffffff;
    --white-soft: rgba(255,255,255,.88);
    --backdrop: #ecebea;
  }
  * { box-sizing: border-box; margin: 0; padding: 0; }
  html, body {
    width: 1200px; height: 900px; overflow: hidden;
    background: var(--backdrop);
    font-family: "Source Sans 3", "Myriad Pro", Arial, sans-serif;
  }
  .canvas { position: relative; width: 1200px; height: 900px; }

  .card { position: absolute; overflow: hidden; box-shadow: 0 6px 18px rgba(0,0,0,.18); }

  /* Front */
  .card-front { left: 238px; top: 62px; width: 555px; height: 343px; background: var(--white); }
  .front-panel { position: absolute; left: 0; top: 0; width: 407px; height: 100%; background: var(--orange); }
  .side-panel { position: absolute; left: 413px; top: 0; right: 0; height: 100%; background: var(--grey); }
  .brand-disc {
    position: absolute; left: 312px; top: 74px; width: 196px; height: 196px;
    border-radius: 50%; background: var(--white);
    display: flex; align-items: center; justify-content: center; text-align: center;
  }
  .brand-disc .brand-name {
    color: var(--grey-dark); font-weight: 700; font-size: 22px; line-height: 1.1; letter-spacing: .5px;
  }
  .contact { position: absolute; left: 32px; top: 46px; color: var(--white); }
  .person-name { font-size: 20px; font-weight: 600; line-height: 24px; }
  .person-title { font-size: 14px; line-height: 18px; color: var(--white-soft); margin-bottom: 10px; letter-spacing: .3px; }
  .contact-row { display: flex; align-items: center; gap: 8px; font-size: 16.5px; line-height: 20px; }
  .contact-row svg { width: 12px; height: 12px; fill: var(--white); flex: none; }
  .address-block { margin-top: 14px; }
  .address-block + .address-block { margin-top: 8px; }
  .address-title { font-size: 18px; font-weight: 600; line-height: 21px; }
  .address-line { font-size: 16.5px; line-height: 20px; }

  /* Back */
  .card-back { left: 457px; top: 518px; width: 560px; height: 344px; background: var(--white); }
  .back-mark {
    position: absolute; left: 50%; top: 74px; width: 112px; height: 112px;
    margin-left: -56px; border-radius: 50%; background: var(--orange);
  }
  .back-brand {
    position: absolute; left: 0; right: 0; top: 212px; text-align: center;
    color: var(--grey-dark); font-weight: 700; text-transform: uppercase;
  }
  .back-brand .line-main { display: block; font-size: 36px; line-height: 38px; letter-spacing: 1px; }
  .back-brand .line-sub { display: block; font-size: 17px; line-height: 22px; letter-spacing: 2px; }
</style>
</head>
<body>
<main class="canvas">

  <section class="card card-front" aria-label="Business card front">
    <div class="front-panel"></div>
    <div class="side-panel"></div>

    <div class="contact">
      <h1 class="person-name">Marcus Hale</h1>
      <div class="person-title">Operations Manager</div>
      <div class="contact-row">
        <svg viewBox="0 0 24 24" aria-hidden="true"><path d="M6.6 10.8a15.1 15.1 0 0 0 6.6 6.6l2.2-2.2a1 1 0 0 1 1-.25 11.4 11.4 0 0 0 3.6.57 1 1 0 0 1 1 1V20a1 1 0 0 1-1 1A17 17 0 0 1 3 4a1 1 0 0 1 1-1h3.5a1 1 0 0 1 1 1c0 1.25.2 2.45.57 3.57a1 1 0 0 1-.25 1z"/></svg>
        <span>055-987 654 321</span>
      </div>
      <div class="contact-row">
        <svg viewBox="0 0 24 24" aria-hidden="true"><path d="M2 5h20v14H2z M2 5l10 8 10-8" /></svg>
        <span>hello@sitemail.com</span>
      </div>

      <div class="address-block">
        <div class="address-title">Shop Address</div>
        <div class="address-line">12345, Address Goes Here</div>
        <div class="address-line">Country Name, 123456.</div>
      </div>
      <div class="address-block">
        <div class="address-title">Mailing Address</div>
        <div class="address-line">12345, Address Goes Here</div>
        <div class="address-line">Country Name, 123456.</div>
      </div>
    </div>

    <div class="brand-disc">
      <span class="brand-name">TANDEM<br>LINE</span>
    </div>
  </section>

  <section class="card card-back" aria-label="Business card back">
    <div class="back-mark"></div>
    <div class="back-brand">
      <span class="line-main">Tandem Line</span>
      <span class="line-sub">Contracting Inc</span>
    </div>
  </section>

</main>
</body>
</html>
```